Zelvo Stationary

Design the stationary of Zelvo Promotions Group.

Zelvo is a BTL company, BTL meaning "below the line". In other words Zelvo is a Promotional Marketing company (the company that design the brands promotional activities).

The design should transmit creativity, agility, boldness.

I need:
* Bis Card
* Letter head
* Envelopes, both vertical and horizontal (for legal size), and letter envelope
* Folders
* PPT template (Title page and regular page)
* CD slip (CD envelope)
* ID card (employee card)

And what ever else you want to throw in.
Updates

Guys,

Something I missed from the brief.   The predominat color should be RED.

Also, have fun and play with the exclamation mark (!) of the logo. 

Hi guys, more comments:

Remember that Zelvo is a "creativity" agency, not in the advertising side but on the promotional side, and that should reflect on the stationary.

 I want a bold design.  Bold and yet crisp.

 

Guys, i just uploaded the Logo in AI format.

I Also uploaded the actual Zelvo Bis Card, wich I like.  So I will like to see some designs with that bis card approach.

Guys, I am so sorry, but I notice in your last post that I upladed a wrong design ("13154_promotions_group_zelvo_brief225630.ai").  The problem was that I asked the designer the file in AI format and he send me thw wrong file, and since I dont have Illustrator I could not verify it.

The differences are minor, I just already ask him the correct one (similar to the EPS file).

Sorry                                   

Just post the correct AI file : "Zelvo Logo.ai"

Reason: I'm expecting more designs to choose from and also I wont be available tomorrow to decide.

Reason: Sorry guys, but we are not there yet!

Target Market(s)

Marketing directors, Marketing Managers

Industry/Entity Type

Legal

Requirements
Must have
• Must work with the logo attached.
The predominat color should be RED.
Play and have fun with the exclamation mark (!).
Should not have
• * No old fonts

Should not be:
* boring
* Informal
* rigid

```html
<!DOCTYPE html>
<html lang="en">
<head>
<meta charset="utf-8">
<title>Zelvo Promotions Group – Stationery</title>
<link rel="stylesheet" href="https://fonts.googleapis.com/css2?family=Montserrat:wght@600;800&family=Open+Sans:wght@400&display=swap">
<style>
  :root {
    --paper: #ffffff;
    --ink: #000000;
    --charcoal: #2b2a2a;
    --red: #8e1517;
    --red-bright: #e0141a;
    --glow-core: #d8141b;
    --glow-mid: #7a0a0e;
    --pattern-dark: #141313;
    --pattern-light: #222020;
    --url-grey: #8a8a8a;
  }
  * { box-sizing: border-box; margin: 0; padding: 0; }
  html, body { width: 778px; height: 1200px; overflow: hidden; background: var(--paper); }
  .sheet { position: relative; width: 778px; height: 1200px; }

  /* presentation cover */
  .cover {
    position: absolute; left: 32px; top: 26px; width: 715px; height: 496px;
    background: var(--ink); overflow: hidden;
  }
  .cover__glow {
    position: absolute; left: 118px; top: 18px; width: 480px; height: 470px;
    border-radius: 50%;
    background: radial-gradient(circle at 50% 48%, var(--glow-core) 0%, #a80d12 35%, var(--glow-mid) 62%, rgba(40,0,0,0.6) 85%, rgba(0,0,0,0) 100%);
  }
  .cover__band {
    position: absolute; left: 0; right: 0; top: 262px; height: 15px;
    background: linear-gradient(180deg, #5a0b0c 0%, #b3161a 50%, #5a0b0c 100%);
  }

  /* brand lockup */
  .lockup { position: absolute; display: flex; align-items: center; gap: 8px; }
  .lockup__text { display: flex; flex-direction: column; }
  .lockup__name {
    font-family: "Montserrat", sans-serif; font-weight: 800; color: var(--ink);
    line-height: 0.9; letter-spacing: -1px;
  }
  .lockup__tag {
    font-family: "Montserrat", sans-serif; font-weight: 600; color: var(--ink);
    text-transform: uppercase; letter-spacing: 3px;
  }
  .lockup__dot { border-radius: 50%; background: var(--red-bright); flex: none; }

  .cover .lockup { left: 268px; top: 226px; }
  .cover .lockup__name { font-size: 56px; }
  .cover .lockup__tag { font-size: 11px; }
  .cover .lockup__dot { width: 22px; height: 22px; }

  /* folder */
  .folder {
    position: absolute; left: 29px; top: 532px; width: 349px; height: 624px;
    background: var(--ink);
  }
  .folder__stripe { position: absolute; left: 0; right: 0; top: 25px; height: 24px; background: var(--red); }
  .folder__pattern {
    position: absolute; left: 0; right: 0; top: 49px; height: 294px;
    background: linear-gradient(180deg, var(--pattern-light), var(--pattern-dark));
  }
  .folder__panel { position: absolute; left: 0; right: 0; top: 343px; height: 260px; background: var(--red); }
  .folder .lockup { left: 55px; top: 115px; }
  .folder .lockup__name { font-size: 44px; }
  .folder .lockup__tag { font-size: 9px; letter-spacing: 2.6px; }
  .folder .lockup__dot { width: 18px; height: 18px; }

  /* envelope */
  .envelope {
    position: absolute; left: 399px; top: 532px; width: 345px; height: 642px;
    background: var(--charcoal);
  }
  .envelope__top { position: absolute; left: 0; right: 0; top: 0; height: 14px; background: var(--ink); }
  .envelope__base { position: absolute; left: 0; right: 0; bottom: 0; height: 101px; background: var(--ink); }
  .envelope .lockup { left: 45px; top: 222px; }
  .envelope .lockup__name { font-size: 46px; }
  .envelope .lockup__tag { font-size: 9.5px; letter-spacing: 2.8px; }
  .envelope .lockup__dot { width: 18px; height: 18px; }
  .envelope__url {
    position: absolute; left: 42px; top: 495px;
    font-family: "Open Sans", sans-serif; font-size: 19px; color: var(--url-grey);
  }
</style>
</head>
<body>
<main class="sheet">

  <section class="cover" aria-label="Presentation title page">
    <div class="cover__glow" role="img" aria-label="Red radial glow with faint damask pattern"></div>
    <div class="cover__band"></div>
    <div class="lockup">
      <div class="lockup__text">
        <span class="lockup__name">zelvo</span>
        <span class="lockup__tag">Promotions Group</span>
      </div>
      <span class="lockup__dot"></span>
    </div>
  </section>

  <section class="folder" aria-label="Folder">
    <div class="folder__stripe"></div>
    <div class="folder__pattern" role="img" aria-label="Dark damask ornamental pattern"></div>
    <div class="folder__panel">
      <div class="lockup">
        <div class="lockup__text">
          <span class="lockup__name">zelvo</span>
          <span class="lockup__tag">Promotions Group</span>
        </div>
        <span class="lockup__dot"></span>
      </div>
    </div>
  </section>

  <section class="envelope" aria-label="Envelope">
    <div class="envelope__top"></div>
    <div class="lockup">
      <div class="lockup__text">
        <span class="lockup__name">zelvo</span>
        <span class="lockup__tag">Promotions Group</span>
      </div>
      <span class="lockup__dot"></span>
    </div>
    <p class="envelope__url">www.zelvo-group.com</p>
    <div class="envelope__base"></div>
  </section>

</main>
</body>
</html>
```